Summit Ridge Business Card

Side 1: Summit Ridge Logo (logo without Maltese cross) with industrial rope rescue related theme. Our company services - TRAINING - Fire Training, Confined Space Rescue Training, Rope Rescue training, Hazmat Training, Incident Command, EMS, Pump Operations Training. Website - summitridgeexample.com.
Side 2: Summit Ridge Fire Department Logo (logo with Maltese cross) with Firefighter related theme. Company (division) services - FIELD SERVICES - Fire Department, Stand-by Rescue, Safety, EMS, Planning. "Serving the Emergency Response Community Since 1982"

Add contact information wherever it makes since (Name, Email, Phone).
I would like it to represent the Summit Ridge Fire Department Logo as a division not as a separate entity without saying it, possibly by depicting it in the background of Side 2 instead of being a standalone picture like the logo on Side 1.

```html
<!DOCTYPE html>
<html lang="en">
<head>
<meta charset="utf-8">
<title>Summit Ridge Business Card</title>
<link rel="stylesheet" href="https://fonts.googleapis.com/css2?family=Montserrat:wght@400;500;600;700;800&display=swap">
<style>
  :root {
    --page: #2b2b2d;
    --charcoal: #3c3c3f;
    --charcoal-light: #4d4d50;
    --red: #e3212b;
    --white: #ffffff;
    --ink: #3a3a3d;
  }
  * { box-sizing: border-box; margin: 0; padding: 0; }
  html, body { width: 1200px; height: 1200px; overflow: hidden; }
  body {
    background: var(--page);
    font-family: "Montserrat", sans-serif;
    position: relative;
  }
  .card {
    position: absolute;
    width: 700px;
    height: 400px;
    left: 250px;
    overflow: hidden;
    box-shadow: 0 14px 30px rgba(0,0,0,.45);
  }

  /* Field services side */
  .card-field { top: 150px; background: var(--white); }
  .field-top {
    position: absolute; inset: 0 0 130px 0;
    background: linear-gradient(135deg, var(--charcoal) 0%, var(--charcoal-light) 45%, var(--charcoal) 100%);
  }
  .brand {
    position: absolute; top: 80px; left: 0; right: 0;
    display: flex; align-items: center; justify-content: center; gap: 16px;
  }
  .brand-dot { width: 22px; height: 22px; border-radius: 50%; background: var(--red); }
  .brand-name { color: var(--white); font-weight: 600; font-size: 40px; letter-spacing: 8px; }
  .brand-rule {
    position: absolute; top: 150px; left: 200px; right: 200px;
    height: 2px; background: var(--red);
  }
  .tagline {
    position: absolute; top: 222px; left: 0; right: 0; text-align: center;
    color: var(--white); font-size: 15px; font-weight: 500; letter-spacing: .6px;
  }
  .field-band {
    position: absolute; left: 0; right: 0; bottom: 0; height: 130px;
    background: linear-gradient(90deg, var(--white), #ececec);
    padding: 32px 60px 0; text-align: center;
    color: var(--ink); font-size: 17px; line-height: 28px; font-weight: 500;
  }
  .label { color: var(--red); font-weight: 600; }

  /* Contact side */
  .card-contact { top: 640px; background: linear-gradient(135deg, var(--white), #ebebeb); }
  .training-strip {
    position: absolute; left: 0; top: 0; width: 230px; height: 400px;
    background: linear-gradient(180deg, var(--charcoal-light), var(--charcoal));
  }
  .training-list {
    position: absolute; left: 0; top: 400px; width: 400px; height: 230px;
    transform-origin: top left; transform: rotate(-90deg);
    display: flex; flex-direction: column; justify-content: center;
    padding: 0 30px;
    color: var(--white); font-size: 15px; line-height: 27px; font-weight: 500;
    text-align: center;
  }
  .contact { position: absolute; left: 290px; top: 50px; right: 40px; color: var(--ink); }
  .person-name { color: var(--red); font-size: 34px; font-weight: 800; }
  .person-role { font-size: 17px; font-weight: 500; margin-top: 4px; }
  .address { margin-top: 58px; font-size: 17px; line-height: 26px; font-weight: 500; }
  .details { margin-top: 16px; list-style: none; font-size: 16px; line-height: 27px; font-weight: 500; }
  .details li { display: flex; align-items: center; gap: 10px; }
  .details svg { width: 15px; height: 15px; fill: var(--red); flex: none; }
</style>
</head>
<body>

<section class="card card-field">
  <div class="field-top">
    <div class="brand">
      <span class="brand-dot"></span>
      <span class="brand-name">SUMMIT RIDGE</span>
    </div>
    <div class="brand-rule"></div>
    <p class="tagline">Serving the Emergency Response Community Since 1982</p>
  </div>
  <div class="field-band">
    <span class="label">FIELD SERVICES</span> - Fire Department | Stand-by Rescue |<br>
    Safety | EMS | Planning
  </div>
</section>

<section class="card card-contact">
  <div class="training-strip">
    <div class="training-list">
      <p><span class="label">TRAINING</span> - Fire Training |</p>
      <p>Confined Space Rescue Training |</p>
      <p>Rope Rescue Training | Hazmat Training |</p>
      <p>Incident Command | EMS |</p>
      <p>Pump Operations Training</p>
    </div>
  </div>
  <div class="contact">
    <h1 class="person-name">Dalton Reyes</h1>
    <p class="person-role">Founder &amp; Director</p>
    <p class="address">120 Harbor Lane<br>Eastport, TX 77000</p>
    <ul class="details">
      <li>
        <svg viewBox="0 0 24 24" aria-hidden="true"><path d="M6.6 10.8a15.1 15.1 0 0 0 6.6 6.6l2.2-2.2c.3-.3.7-.4 1-.2 1.1.4 2.3.6 3.6.6.6 0 1 .4 1 1V20c0 .6-.4 1-1 1A17 17 0 0 1 3 4c0-.6.4-1 1-1h3.5c.6 0 1 .4 1 1 0 1.3.2 2.5.6 3.6.1.3 0 .7-.2 1z"/></svg>
        (555) 013-2846
      </li>
      <li>
        <svg viewBox="0 0 24 24" aria-hidden="true"><path d="M2 5h20v14H2zm2 2v.5l8 5 8-5V7l-8 5z"/></svg>
        reyes@summitridgeexample.com
      </li>
      <li>
        <svg viewBox="0 0 24 24" aria-hidden="true"><path d="M12 2a10 10 0 1 0 0 20 10 10 0 0 0 0-20zm6.9 6h-3a15 15 0 0 0-1.3-4 8 8 0 0 1 4.3 4zM12 4c.8 1.2 1.5 2.5 1.9 4h-3.8c.4-1.5 1.1-2.8 1.9-4zM4.3 14a8 8 0 0 1 0-4h3.4a16 16 0 0 0 0 4zm.8 2h3a15 15 0 0 0 1.3 4 8 8 0 0 1-4.3-4zm3-8h-3a8 8 0 0 1 4.3-4A15 15 0 0 0 8.1 8zM12 20c-.8-1.2-1.5-2.5-1.9-4h3.8c-.4 1.5-1.1 2.8-1.9 4zm2.3-6H9.7a14 14 0 0 1 0-4h4.6a14 14 0 0 1 0 4zm.3 6a15 15 0 0 0 1.3-4h3a8 8 0 0 1-4.3 4zm1.7-6a16 16 0 0 0 0-4h3.4a8 8 0 0 1 0 4z"/></svg>
        www.summitridgeexample.com
      </li>
    </ul>
  </div>
</section>

</body>
</html>
```